Business Card Re-Design/Update

We'd like to update out business cards. I've included our current "Style guide" which has the colour scheme of the organisation in it. I've also included the branding files with logos etc in them.

I've also included a copy of one of our existing cards so that you can see how ugly/dated they look. I'd like a fresh modern corporate look.

Target Market(s)

These are for our clients, potential clients, industry contacts - like all business cards

Contact Information for Business Card

Name
Position
Company Address - Level 1, 47 Fernby Street, Carlow Qld 4072
Direct Phone
mobile
Email
Website -www.korvalit.com.au
Logo

Colors

Designer to choose colors to be used in the design.

Requirements
Must have
• Main Logo
• Cards will need to be editable to be able to personalize them for each new employee.
Nice to have
• The MapOut, ShipWell, KeepSteady would be okay to have if they can be sensibly and professionally added to the look without detracting from the main imagery.
• Maybe they could go on the back of the card? will leave this to your creative discretion as to whether/where they fit.
Should not have
• Should not have decorative or script fonts

```html
<!DOCTYPE html>
<html lang="en">
<head>
<meta charset="utf-8">
<title>korvalIT business card</title>
<link href="https://fonts.googleapis.com/css2?family=Arimo:wght@400;700&display=swap" rel="stylesheet">
<style>
  :root {
    --brand-red: #b3151c;
    --brand-red-light: #d01d24;
    --brand-red-dark: #8f0c12;
    --ink: #231f20;
    --ink-soft: #555555;
    --paper: #f7f7f7;
    --backdrop: #e4e4e4;
    --white: #ffffff;
  }
  * { margin: 0; padding: 0; box-sizing: border-box; }
  html, body {
    width: 1200px;
    height: 960px;
    overflow: hidden;
    background: var(--backdrop);
    font-family: "Arimo", Arial, sans-serif;
  }
  .canvas { position: relative; width: 1200px; height: 960px; }

  .card { position: absolute; width: 602px; height: 343px; overflow: hidden; }

  /* Front */
  .card--front { left: 314px; top: 113px; background: var(--paper); }
  .brand {
    position: absolute;
    display: flex;
    align-items: center;
    gap: 14px;
  }
  .brand__mark { display: block; background: var(--brand-red); }
  .brand__name { font-weight: 700; letter-spacing: -0.5px; line-height: 1; }
  .card--front .brand { right: 48px; top: 62px; }
  .card--front .brand__mark { width: 34px; height: 34px; }
  .card--front .brand__name { font-size: 38px; color: var(--ink); }

  .person { position: absolute; left: 43px; top: 206px; }
  .person__name {
    font-size: 20px; font-weight: 700; color: var(--brand-red);
    text-transform: uppercase; letter-spacing: -0.2px;
  }
  .person__role { margin-top: 3px; margin-left: 2px; font-size: 14.5px; color: var(--ink); }

  .contact { position: absolute; left: 329px; top: 157px; font-size: 14px; color: var(--ink-soft); line-height: 19px; }
  .contact__address { margin-bottom: 10px; width: 200px; }
  .contact__list { list-style: none; margin-left: 3px; }
  .contact__label { font-weight: 700; color: var(--brand-red); }

  .web-band { position: absolute; left: 0; bottom: 0; width: 304px; height: 37px; }
  .web-band__text {
    position: absolute; left: 44px; bottom: 11px;
    font-size: 13.5px; color: var(--white); letter-spacing: 1.2px;
  }

  /* Back */
  .card--back {
    left: 311px; top: 472px; width: 600px;
    background: radial-gradient(ellipse 70% 80% at 45% 40%, var(--brand-red-light) 0%, var(--brand-red) 55%, var(--brand-red-dark) 100%);
  }
  .card--back .brand { left: 104px; top: 140px; gap: 18px; }
  .card--back .brand__mark { width: 56px; height: 56px; background: var(--white); }
  .card--back .brand__name { font-size: 50px; color: var(--white); }

  .services {
    position: absolute; left: 52px; right: 52px; top: 278px;
    display: flex; justify-content: space-between; list-style: none;
  }
  .service { display: flex; align-items: center; gap: 8px; font-size: 25px; font-weight: 700; color: var(--white); letter-spacing: -0.3px; }
  .service__mark { width: 20px; height: 20px; background: var(--white); }
</style>
</head>
<body>
<main class="canvas">

  <section class="card card--front" aria-label="Business card front">
    <div class="brand">
      <span class="brand__mark"></span>
      <span class="brand__name">korvalIT</span>
    </div>

    <div class="person">
      <p class="person__name">Maren Holt</p>
      <p class="person__role">Business Development Manager</p>
    </div>

    <div class="contact">
      <p class="contact__address">Level 1, 47 Fernby Street<br>Carlow Qld 4072</p>
      <ul class="contact__list">
        <li><span class="contact__label">P:</span> +61 (0)7 3900 4120</li>
        <li><span class="contact__label">P:</span> +61 (0)7 3900 4127</li>
        <li><span class="contact__label">C:</span> +61 (0)412 506 389</li>
        <li><span class="contact__label">F:</span> +61 (0)7 3900 4199</li>
        <li><span class="contact__label">E:</span> mholt@korvalit.com.au</li>
      </ul>
    </div>

    <div class="web-band">
      <svg width="304" height="37" viewBox="0 0 304 37" aria-hidden="true">
        <defs>
          <linearGradient id="bandFill" x1="0" y1="0" x2="1" y2="0">
            <stop offset="0" stop-color="#a3121a"/>
            <stop offset="1" stop-color="#c41a21"/>
          </linearGradient>
        </defs>
        <polygon points="0,0 272,0 304,37 0,37" fill="url(#bandFill)"/>
      </svg>
      <span class="web-band__text">www.korvalit.com.au</span>
    </div>
  </section>

  <section class="card card--back" aria-label="Business card back">
    <div class="brand">
      <span class="brand__mark"></span>
      <span class="brand__name">korvalIT</span>
    </div>

    <ul class="services">
      <li class="service"><span class="service__mark"></span>MapOut</li>
      <li class="service"><span class="service__mark"></span>ShipWell</li>
      <li class="service"><span class="service__mark"></span>KeepSteady</li>
    </ul>
  </section>

</main>
</body>
</html>
```